Fitness Business Card Design Needed

We are looking for a business card design that stands out but is also simple and unique. I like the idea of on one side using the picture of myself with my logo at my feet. I love the texture on the business card so please take that into account when designing. Then on the other side having my contact details. I want it to be clean, modern, and pretty. I am open to designs that allow spot gloss or gold foiling.

Contact Information for Business Card

Space for Name, Phone number, email, and website

```html
<!DOCTYPE html>
<html lang="en">
<head>
<meta charset="utf-8">
<title>PetitePower Fitness – Business Card</title>
<link rel="stylesheet" href="https://fonts.googleapis.com/css2?family=Montserrat:wght@400&family=Roboto:ital,wght@0,400;0,500;0,700;1,400&display=swap">
<style>
  :root {
    --stage: #e9e8e6;
    --card: #ffffff;
    --gold: #b8893a;
    --ink: #3a3a3a;
    --rule: #8c8c8c;
    --photo-light: #f1e4d6;
    --photo-mid: #d9a27f;
    --photo-warm: #d9543a;
  }
  * { box-sizing: border-box; margin: 0; padding: 0; }
  html, body { width: 1200px; height: 801px; overflow: hidden; }
  body {
    background: var(--stage);
    font-family: "Roboto", Arial, sans-serif;
    position: relative;
  }
  .card {
    position: absolute;
    width: 540px;
    height: 309px;
    background: var(--card);
    box-shadow: 0 6px 18px rgba(0,0,0,.18);
    overflow: hidden;
  }
  .card--front { left: 40px; top: 246px; }
  .card--back  { left: 620px; top: 246px; }

  /* Brand name with a plain square mark above it */
  .brand {
    position: absolute;
    display: flex;
    flex-direction: column;
    align-items: center;
    color: var(--gold);
    font-family: "Montserrat", Arial, sans-serif;
    font-weight: 400;
    white-space: nowrap;
    line-height: 1;
  }
  .brand__mark {
    border: 1.5px solid var(--gold);
    transform: rotate(45deg);
    flex: none;
  }

  /* Front side */
  .portrait {
    position: absolute;
    left: 58px;
    top: 14px;
    width: 150px;
    height: 295px;
    background: linear-gradient(180deg, var(--photo-light) 0%, var(--photo-mid) 45%, var(--photo-warm) 62%, var(--photo-mid) 80%, #cdb89a 100%);
    border-radius: 60px 60px 4px 4px;
    opacity: .9;
  }
  .brand--front {
    left: 225px;
    right: 15px;
    top: 112px;
    font-size: 17px;
    letter-spacing: 2px;
    gap: 26px;
  }
  .brand--front .brand__mark { width: 44px; height: 44px; }

  /* Back side */
  .brand--back {
    right: 28px;
    top: 46px;
    font-size: 13px;
    letter-spacing: 1.5px;
    gap: 16px;
  }
  .brand--back .brand__mark { width: 26px; height: 26px; }

  .holder {
    position: absolute;
    left: 36px;
    top: 108px;
  }
  .holder__name {
    color: var(--gold);
    font-weight: 500;
    font-size: 23px;
    letter-spacing: .3px;
    line-height: 1;
  }
  .holder__title {
    margin-top: 6px;
    color: var(--ink);
    font-size: 15px;
    line-height: 1;
  }
  .divider {
    position: absolute;
    left: 36px;
    right: 40px;
    top: 162px;
    border-top: 1px solid var(--rule);
  }
  .contacts {
    position: absolute;
    left: 36px;
    top: 176px;
    list-style: none;
    font-size: 14px;
    font-style: italic;
    color: var(--ink);
    line-height: 20px;
  }
  .contacts li { display: flex; align-items: center; gap: 8px; }
  .contacts svg { width: 12px; height: 12px; fill: var(--gold); flex: none; }
  .address {
    position: absolute;
    right: 40px;
    bottom: 30px;
    text-align: right;
    font-size: 15px;
    font-style: normal;
    color: var(--ink);
    line-height: 21px;
  }
</style>
</head>
<body>

<section class="card card--front" aria-label="Business card front">
  <div class="portrait" role="img" aria-label="Full-length photo of the trainer in a red swimsuit standing on sand"></div>
  <div class="brand brand--front">
    <span class="brand__mark"></span>
    <span class="brand__name">PETITEPOWER FITNESS</span>
  </div>
</section>

<section class="card card--back" aria-label="Business card back">
  <div class="brand brand--back">
    <span class="brand__mark"></span>
    <span class="brand__name">PETITEPOWER FITNESS</span>
  </div>

  <div class="holder">
    <p class="holder__name">LENA ORTIZ</p>
    <p class="holder__title">FITNESS TRAINER</p>
  </div>

  <div class="divider"></div>

  <ul class="contacts">
    <li>
      <svg viewBox="0 0 24 24" aria-hidden="true"><path d="M6.6 10.8a15.1 15.1 0 0 0 6.6 6.6l2.2-2.2a1 1 0 0 1 1-.25 11.4 11.4 0 0 0 3.6.57 1 1 0 0 1 1 1V20a1 1 0 0 1-1 1A17 17 0 0 1 3 4a1 1 0 0 1 1-1h3.5a1 1 0 0 1 1 1c0 1.25.2 2.45.57 3.57a1 1 0 0 1-.25 1z"/></svg>
      555 014 2287
    </li>
    <li>
      <svg viewBox="0 0 24 24" aria-hidden="true"><path d="M2 5h20v14H2zm2 2v.4l8 5 8-5V7zm0 2.8V17h16V9.8l-8 5z"/></svg>
      hello@petitepower.com
    </li>
    <li>
      <svg viewBox="0 0 24 24" aria-hidden="true"><circle cx="12" cy="12" r="10"/></svg>
      www.petitepower.com
    </li>
  </ul>

  <address class="address">
    214 Willow Crest Road<br>
    Juneau, Alaska 99801
  </address>
</section>

</body>
</html>
```